Business card design for holistic health care clinic

We need a double-sided business card design for our holistic health care clinic that integrates our logo design and also its color scheme. My business is called Valmira. It is an integrative medicine clinic. You have already done the logo for me. Please ensure an elegant and upscale design that is not cluttered, but still has all the necessary information (please see below for details).

Target Market(s)

Wellness, fitness, rehabilitation for educated, well-traveled open-minded clients who are focused on natural, organic, balanced and preventive healthcare and lifestyle.

Industry/Entity Type

Medical

Contact Information for Business Card

Modern, clean.

Number of Pages Required

1 page

Font styles to use
Serif
Sans Serif

Colors

Designer to choose colors to be used in the design.

Requirements
Must have
• Logo on one side, all other information on the other side.
• Other information should include:
• Tobias Wrenfeld - DOE, CPT, LMT
• 4100 East Marrow Drive
• Austin, TX 78119
• 512 555 0148
• 818 555 0192
• info@ValmiraHealth.example
• t.wrenfeld@ValmiraHealth.example
Nice to have
• Darker background on front - but not totally black - shaded/dark gray.

```html
<!DOCTYPE html>
<html lang="en">
<head>
<meta charset="utf-8">
<title>Valmira – Business Card</title>
<link rel="stylesheet" href="https://fonts.googleapis.com/css2?family=Open+Sans:wght@400;600;700&family=PT+Sans+Narrow:wght@700&display=swap">
<style>
  :root {
    --backdrop: #5b4636;
    --card: #2b2b2c;
    --card-edge: #252526;
    --brand-blue: #0a8dc9;
    --brand-blue-deep: #1d3c4c;
    --text-light: #e9e9e9;
  }
  * { margin: 0; padding: 0; box-sizing: border-box; }
  html, body {
    width: 1200px; height: 808px; overflow: hidden;
    background: var(--backdrop);
  }
  .stage { position: relative; width: 1200px; height: 808px; }
  .card {
    position: absolute; top: 260px;
    width: 505px; height: 289px;
    background: linear-gradient(180deg, var(--card) 0%, var(--card-edge) 100%);
    box-shadow: 0 3px 6px rgba(0,0,0,0.45);
    overflow: hidden;
  }
  .card--front { left: 94px; }
  .card--back { left: 610px; }

  .emblem-area { position: absolute; top: 0; height: 289px; }
  .card--front .emblem-area { left: 216px; width: 289px; }
  .card--back .emblem-area { left: 0; width: 290px; }

  .holder { position: absolute; left: 23px; top: 114px; }
  .holder__name {
    font-family: "PT Sans Narrow", "Arial Narrow", sans-serif;
    font-weight: 700; font-size: 18px; letter-spacing: 0.2px;
    color: var(--brand-blue); line-height: 1;
  }
  .holder__credentials {
    font-family: "PT Sans Narrow", "Arial Narrow", sans-serif;
    font-weight: 700; font-size: 10px;
    color: var(--brand-blue); margin-top: 3px;
  }

  .address {
    position: absolute; left: 21px; top: 164px;
    font-family: "Open Sans", sans-serif; font-size: 12.5px;
    color: var(--text-light); line-height: 17px; font-style: normal;
  }
  .contacts {
    position: absolute; left: 21px; top: 203px; list-style: none;
    font-family: "Open Sans", sans-serif; font-size: 12.5px;
    color: var(--text-light); line-height: 16px;
  }
  .contacts li { display: flex; align-items: center; gap: 6px; }
  .contacts svg { width: 12px; height: 12px; fill: var(--brand-blue); flex: none; }

  .brand {
    position: absolute; left: 286px; top: 189px; width: 192px;
    text-align: center; font-family: "Open Sans", sans-serif;
  }
  .brand__name {
    font-weight: 700; font-size: 35px; line-height: 1;
    letter-spacing: 0.5px; color: var(--brand-blue);
  }
  .brand__descriptor {
    font-weight: 600; font-size: 11px; color: var(--brand-blue);
    margin-top: 3px;
  }
  .brand__tagline {
    font-weight: 600; font-size: 13px; color: #ffffff; margin-top: 1px;
  }
</style>
</head>
<body>
<main class="stage">

  <section class="card card--front" aria-label="Card front">
    <div class="emblem-area" role="img" aria-label="Large blue winged brand emblem"
         style="background: radial-gradient(ellipse 70% 55% at 70% 40%, rgba(10,141,201,0.85) 0%, rgba(10,141,201,0.35) 55%, rgba(10,141,201,0) 80%);"></div>

    <div class="holder">
      <p class="holder__name">TOBIAS WRENFELD</p>
      <p class="holder__credentials">DOE, CPT, LMT</p>
    </div>

    <address class="address">
      4100 East Marrow Drive<br>
      Austin, TX 78119
    </address>

    <ul class="contacts">
      <li>
        <svg viewBox="0 0 12 12" aria-hidden="true"><path d="M1 4.5C1 2.5 3 1.5 6 1.5s5 1 5 3l-2.5.6-.5-1.3H4l-.5 1.3zM3 6h6l1.5 4.5h-9z"/></svg>
        <span>512 555 0148</span>
      </li>
      <li>
        <svg viewBox="0 0 12 12" aria-hidden="true"><path d="M3.5 0.5h5a1 1 0 0 1 1 1v9a1 1 0 0 1-1 1h-5a1 1 0 0 1-1-1v-9a1 1 0 0 1 1-1zM4 2v7h4V2zm2 7.6a.6.6 0 1 0 0 1.2.6.6 0 0 0 0-1.2z"/></svg>
        <span>818 555 0192</span>
      </li>
      <li>
        <svg viewBox="0 0 12 12" aria-hidden="true"><path d="M0.5 3h11v6.5h-11zM1.3 3.6 6 7l4.7-3.4z" fill-rule="evenodd"/></svg>
        <span>t.wrenfeld@ValmiraHealth.example</span>
      </li>
      <li>
        <svg viewBox="0 0 12 12" aria-hidden="true"><circle cx="6" cy="6" r="5.5"/><path d="M3 3.5c1 0 1.5 1 2.5 1s.5 1.5-.5 2-1 1.5-1.5 2.5C2.5 8 2 6 3 3.5zM7.5 6c1 0 1.5.8 1.5 2-.8.6-1.5.2-1.8-.5z" fill="#2b2b2c"/></svg>
        <span>www.ValmiraHealth.example</span>
      </li>
    </ul>
  </section>

  <section class="card card--back" aria-label="Card back">
    <div class="emblem-area" role="img" aria-label="Faint dark blue winged brand emblem"
         style="background: radial-gradient(ellipse 70% 55% at 30% 40%, rgba(29,60,76,0.9) 0%, rgba(29,60,76,0.4) 55%, rgba(29,60,76,0) 80%);"></div>

    <div class="brand">
      <p class="brand__name">VALMIRA</p>
      <p class="brand__descriptor">Integrative Holistic Medicine</p>
      <p class="brand__tagline">helping the body help itself</p>
    </div>
  </section>

</main>
</body>
</html>
```